Brightwell Supports

We need an updated website that captures the comprehensive services and supports we provide to persons with developmental disabilities. We need a website design that educates families about the services we provide. We would also need a website that is user-friendly so that we could periodically update training schedules and ongoing programming.

• Thank you for submitting designs.  A few things I am hoping to see offered in the website:
• Front page highlights the services we offer (host homes, family caregiver, day program, employment program, SLS program, supported apartment program, behavior/clinical program)
• Front page also highlights any new programs we want to make prominent:  family caregiver, future restaurant employment openings, etc...
• Interactive Training Calendar
• Employee Resources page (link to carevo, email login, etc.)
• Uniform provider application for host home providers
• Information on agency - history, goals, etc.
• Contact Information/Location

 

Fun things to include:

• Client Highlights (featuring a client story each month, etc...)
• Employee highlights (featuring a staff member...)
• link to other Brightwell business pages (Brightwell Therapy and Brightwell Restaurant)

```html
<!DOCTYPE html>
<html lang="en">
<head>
<meta charset="utf-8">
<title>Brightwell Supports</title>
<link rel="stylesheet" href="https://fonts.googleapis.com/css2?family=Open+Sans:wght@400;600;700&family=Source+Sans+3:wght@600&display=swap">
<style>
:root{
  --page:#ececec;
  --panel:#ffffff;
  --frame:#dcdcdc;
  --brand:#8a2a2b;
  --brand-dark:#7a2223;
  --ink:#2f2f2f;
  --body:#7b7b7b;
  --rule:#d2d2d2;
  --band:#dadada;
}
*{box-sizing:border-box;margin:0;padding:0}
html,body{width:1074px;height:1200px;overflow:hidden}
body{background:var(--page);font-family:"Open Sans",Arial,sans-serif;color:var(--body);position:relative}
.abs{position:absolute}
.brand-name{left:0;width:1074px;top:44px;text-align:center;font-family:"Source Sans 3",Arial,sans-serif;font-weight:600;font-size:26px;color:var(--brand);display:flex;justify-content:center;align-items:center;gap:10px}
.brand-name .dot{width:14px;height:14px;border-radius:50%;background:var(--brand)}
.nav{left:254px;top:112px;width:566px;height:44px;background:var(--panel);display:flex;justify-content:space-between;align-items:center;padding:0 18px 0 16px}
.nav a{font-size:10.6px;font-weight:700;color:var(--brand);text-decoration:none}
.slider-base{left:254px;top:400px;width:566px;height:56px;background:var(--panel)}
.slider{left:193px;top:155px;width:688px;height:259px;background:var(--frame);box-shadow:0 8px 8px -4px rgba(0,0,0,.25)}
.slide-photo{left:201px;top:162px;width:673px;height:244px;background:linear-gradient(90deg,#f4f5f7 0%,#e6eaef 35%,#b9c3cf 65%,#8a96a4 100%)}
.tagline{left:244px;top:242px;font-family:"Source Sans 3",Arial,sans-serif;font-weight:600;font-size:17.6px;line-height:29px;color:var(--ink)}
.dots{left:517px;top:429px;display:flex;gap:4px}
.dots span{width:10px;height:10px;border-radius:50%;background:#d9d9d9}
.dots span.on{background:var(--brand)}
h2{font-family:"Source Sans 3",Arial,sans-serif;font-weight:600;font-size:14.6px;color:var(--ink);position:absolute}
.thumb{position:absolute;background:var(--panel);box-shadow:0 1px 2px rgba(0,0,0,.15);padding:6px}
.thumb div{width:100%;height:100%}
.copy{position:absolute;font-size:9.1px;line-height:12.8px;text-align:justify}
.more{position:absolute;width:53px;height:21px;background:var(--brand);color:#fff;font-size:9px;line-height:21px;padding-left:14px}
.rule{left:193px;top:746px;width:688px;height:1px;background:var(--rule)}
.news{position:absolute;left:193px;width:216px}
.date{position:absolute;left:1px;top:0;width:36px;height:36px;background:var(--brand);color:#fff;font-size:8.6px;font-weight:700;line-height:10px;text-align:center;padding-top:8px;border-radius:2px}
.news h3{position:absolute;left:58px;top:-2px;font-size:9px;font-weight:700;color:var(--brand)}
.news p{position:absolute;left:58px;top:13px;font-size:8.8px;line-height:14.4px;width:160px}
.news .sep{position:absolute;left:0;top:56px;width:216px;height:1px;background:var(--rule)}
.prog{font-size:8.8px;line-height:14.4px}
.band{left:0;top:1076px;width:1074px;height:7px;background:var(--band)}
.foot{left:194px;font-size:7.8px;color:#6e6e6e}
.foot span{margin:0 4px;color:#9a9a9a}
.social{left:774px;top:1111px;display:flex;gap:14px}
.social span{width:16px;height:16px;border-radius:50%;background:#9d9d9d}
</style>
</head>
<body>

<div class="abs brand-name"><span class="dot"></span>Brightwell Supports</div>

<div class="abs slider-base"></div>
<nav class="abs nav">
  <a>Home</a><a>Services</a><a>Programs</a><a>Become a Provider</a><a>Employee Resources</a><a>Team</a><a>Contact Us</a>
</nav>

<div class="abs slider"></div>
<div class="abs slide-photo" role="img" aria-label="Two colleagues reviewing papers at a laptop in a bright office"></div>
<div class="abs tagline">Building Abilities<br>Creating Opportunities<br>Developing Relationships</div>
<div class="abs dots"><span class="on"></span><span></span><span></span></div>

<h2 style="left:193px;top:494px">Host Home Services</h2>
<h2 style="left:373px;top:494px">Respite Services</h2>
<h2 style="left:554px;top:494px">Mentor Services</h2>
<h2 style="left:735px;top:494px">Supported Services</h2>

<div class="thumb" style="left:193px;top:530px;width:146px;height:78px"><div role="img" aria-label="Hands holding a small model house" style="background:linear-gradient(90deg,#c98f78,#8a3b30 50%,#c98f78)"></div></div>
<div class="thumb" style="left:373px;top:530px;width:146px;height:78px"><div role="img" aria-label="Caregiver sitting with an elderly woman" style="background:linear-gradient(90deg,#9aa4ad,#d7cbbd 55%,#b9bec4)"></div></div>
<div class="thumb" style="left:554px;top:530px;width:146px;height:78px"><div role="img" aria-label="Group of people talking around a table" style="background:linear-gradient(90deg,#5e6672,#b6c2d0 50%,#4c5562)"></div></div>
<div class="thumb" style="left:735px;top:530px;width:146px;height:78px"><div role="img" aria-label="Two professionals standing in an office" style="background:linear-gradient(90deg,#c8d3df,#34404e 55%,#dde3ea)"></div></div>

<p class="copy" style="left:194px;top:619px;width:145px">Community based residential service options for adults with developmental and cognitive disabilities.</p>
<p class="copy" style="left:374px;top:619px;width:145px">Respite is provided on a short-term basis by trained Brightwell Supports respite providers. Respite is provided</p>
<p class="copy" style="left:554px;top:619px;width:145px">Mentors with Brightwell Supports promote self-advocacy of clients through direct and specific instructional methods,</p>
<p class="copy" style="left:735px;top:619px;width:146px">Brightwell Supports provides intensive and ongoing supports that enable clients that may otherwise</p>

<a class="more" style="left:193px;top:688px">More</a>
<a class="more" style="left:372px;top:688px">More</a>
<a class="more" style="left:555px;top:688px">More</a>
<a class="more" style="left:735px;top:688px">More</a>

<div class="abs rule"></div>

<h2 style="left:193px;top:774px">Latest News</h2>
<h2 style="left:443px;top:774px">Day/Employment Program</h2>
<h2 style="left:673px;top:774px">Residential Program</h2>

<div class="news" style="top:811px">
  <div class="date">01 Apr<br>2014</div>
  <h3>Cumque nihil impedit</h3>
  <p>Cuo minus id, quod maxime placeat facere possimus, menda est.</p>
  <div class="sep"></div>
</div>
<div class="news" style="top:891px">
  <div class="date">14 Mar<br>2014</div>
  <h3>Lorem ipsum dolor</h3>
  <p>Sed do eiusmod tempor incididunt ut labore et dolore magna aliqua.</p>
  <div class="sep"></div>
</div>
<div class="news" style="top:971px">
  <div class="date">20 Feb<br>2014</div>
  <h3>Duis aute irure</h3>
  <p>Voluptate velit esse cillum dolore eu fugiat nulla pariatur.</p>
</div>

<div class="thumb" style="left:442px;top:807px;width:203px;height:79px"><div role="img" aria-label="Day program room with tables and red chairs" style="background:linear-gradient(180deg,#6a5547,#d9d9d9 55%,#5b3e2e)"></div></div>
<div class="thumb" style="left:673px;top:807px;width:202px;height:79px"><div role="img" aria-label="Living room with sofa and bright window" style="background:linear-gradient(90deg,#3c2a22,#7a6659 40%,#e8e3da 60%,#4a3326)"></div></div>

<p class="copy prog" style="left:442px;top:901px;width:205px">Brightwell Supports offers a variety of programming, including employment services, community outings, 1:1 services and rehabilitative services. Our day program is located in North Alderton and we provide services to clients living throughout Cedar and Marlow Counties.</p>
<p class="copy prog" style="left:673px;top:901px;width:208px">Brightwell Supports focuses on independence while supporting our providers and clients. As an agency we address any mental health issues in addition to behavioral needs. We are a small and stable agency based out of Alderton providing Residential, Day Program, Employment and SLS services</p>

<a class="more" style="left:442px;top:1006px">More</a>
<a class="more" style="left:673px;top:1006px">More</a>

<div class="abs band"></div>
<div class="abs foot" style="top:1105px">Welcome<span>|</span>Available Services<span>|</span>Residential Program<span>|</span>Day/Employment Program<span>|</span>SLS Program<span>|</span>Become a Provider</div>
<div class="abs foot" style="top:1124px">Employee Resources<span>|</span>Meet Our Team!<span>|</span>Activity Calendar<span>|</span>Training Calendar<span>|</span>Contact Us<span>|</span>Location<span>|</span>Community Resources</div>
<div class="abs foot" style="top:1145px">© Copyright 2014 Brightwell Supports<span>|</span>All Rights Reserved</div>
<div class="abs social" aria-label="Social links"><span></span><span></span><span></span></div>

</body>
</html>
```